Business Card for Industrial Distributor

We need a business card design for an industrial distributor. We sell machine parts for the manufacturing and oil industry. We would like the cards to look clean and modern but with a touch of industry.

Our colors are blue/white.

Please feel free to visit our website www.korvelpartsco.com

Target Market(s)

mexican manufacturers in the automobile/aerospace industry

Industry/Entity Type

Industrial

Colors
ffffff
0555a3

```html
<!DOCTYPE html>
<html lang="en">
<head>
<meta charset="utf-8">
<title>Korvel Business Card</title>
<link rel="stylesheet" href="https://fonts.googleapis.com/css2?family=Montserrat:wght@400;500;600;700&display=swap">
<style>
  :root {
    --stage: #2a2a2c;
    --card-black: #050505;
    --brand-blue: #0555a3;
    --bright-blue: #1a7fd0;
    --logo-blue: #2d3fb0;
    --white: #ffffff;
  }
  * { margin: 0; padding: 0; box-sizing: border-box; }
  html, body { width: 1200px; height: 900px; overflow: hidden; }
  body {
    background: var(--stage);
    font-family: "Montserrat", sans-serif;
    position: relative;
  }
  .card {
    position: absolute;
    width: 560px;
    height: 320px;
    border-radius: 22px;
    background: var(--card-black);
    overflow: hidden;
  }
  .card-front { left: 90px; top: 90px; }
  .card-back { left: 550px; top: 490px; }

  /* Front */
  .brand-lockup {
    position: absolute;
    left: 70px; top: 110px;
    display: flex; align-items: center; gap: 16px;
  }
  .brand-dot {
    width: 78px; height: 78px; border-radius: 50%;
    background: var(--logo-blue);
  }
  .brand-name {
    font-weight: 700; font-size: 78px; letter-spacing: 1px;
    color: var(--logo-blue); line-height: 1;
  }
  .front-web {
    position: absolute; left: 0; right: 0; bottom: 34px;
    text-align: center; font-size: 19px; font-weight: 500;
    color: var(--bright-blue);
  }
  .front-web .domain { color: var(--white); font-weight: 600; }

  /* Back */
  .back-art { position: absolute; inset: 0; }
  .contact {
    position: absolute; left: 58px; top: 118px;
    color: var(--white);
  }
  .contact-name {
    font-weight: 700; font-size: 23px; line-height: 1.2; color: var(--bright-blue);
  }
  .contact-title { font-size: 14px; margin: 0 0 12px 16px; }
  .contact-address { font-size: 15px; line-height: 1.3; margin-left: 24px; }
  .contact-list { list-style: none; margin: 10px 0 0 24px; font-size: 15px; line-height: 1.35; }
  .contact-list li { display: flex; align-items: center; gap: 10px; white-space: nowrap; }
  .contact-list svg { width: 11px; height: 11px; flex: none; }
  .contact-list .accent { color: var(--bright-blue); }
</style>
</head>
<body>
  <section class="card card-front">
    <div class="brand-lockup">
      <div class="brand-dot"></div>
      <div class="brand-name">Korvel</div>
    </div>
    <p class="front-web">www.<span class="domain">korvelpartsco</span>.com</p>
  </section>

  <section class="card card-back">
    <svg class="back-art" viewBox="0 0 560 320" width="560" height="320">
      <circle cx="446" cy="102" r="172" fill="var(--brand-blue)"/>
      <circle cx="452" cy="98" r="168" fill="var(--white)"/>
      <circle cx="462" cy="105" r="76" fill="var(--logo-blue)"/>
      <path d="M0 190 H14 a12 12 0 0 1 12 12 V320 H0 Z" fill="var(--bright-blue)"/>
    </svg>
    <div class="contact">
      <h1 class="contact-name">Marco Delgado</h1>
      <p class="contact-title">Director</p>
      <p class="contact-address">P.O. Box 4410<br>Lansing, MI 48901</p>
      <ul class="contact-list">
        <li><svg viewBox="0 0 12 12"><path d="M2 1 L4 1 L5 4 L3.6 5 A7 7 0 0 0 7 8.4 L8 7 L11 8 L11 10 A1 1 0 0 1 10 11 A9 9 0 0 1 1 2 A1 1 0 0 1 2 1Z" fill="var(--bright-blue)"/></svg><span>+330 5518-2093</span></li>
        <li><svg viewBox="0 0 12 12"><rect x="1" y="2.5" width="10" height="7" fill="none" stroke="var(--bright-blue)" stroke-width="1.3"/><path d="M1 2.5 L6 6.5 L11 2.5" fill="none" stroke="var(--bright-blue)" stroke-width="1.3"/></svg><span>info@korvelpartsco.com</span></li>
        <li><svg viewBox="0 0 12 12"><circle cx="6" cy="6" r="5" fill="none" stroke="var(--bright-blue)" stroke-width="1.3"/><path d="M1 6 H11 M6 1 C3 4 3 8 6 11 C9 8 9 4 6 1" fill="none" stroke="var(--bright-blue)" stroke-width="1"/></svg><span>www.<span class="accent">korvelpartsco</span>.com</span></li>
      </ul>
    </div>
  </section>
</body>
</html>
```